Business Card Design

Buy and sell properties
Buy and rehab properties
Buy properties for cash
That is what I do but do need a logo
looking for some type of logo or design on it
Just started business
Back of card should say something like BUY HOUSES CASH
Overview: it is a new company. Basically I buy properties wholesale and fix them up and sell them or sell them to other fix and flippers
Background: company is new so not any background
Market: is basically anyone selling a house or buying a house. Someone that needs to sell house fast. Basically I am a cash home buyer!!!

Updates
Email on card should be:   harborlanerealtyinc@mailnest.com

Industry/Entity Type
House
Contact Information for Business Card
Harbor Lane Realty Inc
PO Box 718296
Coral Mill Key FL 33071

Dwight Kallum
dkallum@mailnest.com
305-271-5589

```html
<!DOCTYPE html>
<html lang="en">
<head>
<meta charset="utf-8">
<title>Harbor Lane Realty Inc — Business Card</title>
<link rel="stylesheet" href="https://fonts.googleapis.com/css2?family=Roboto:wght@300;700&family=Roboto+Condensed:wght@700&display=swap">
<style>
  :root {
    --paper: #ffffff;
    --ink: #111111;
    --gold: #f0b81c;
    --gold-deep: #e0a514;
    --stage: #ece9e4;
  }
  * { box-sizing: border-box; margin: 0; padding: 0; }
  html, body {
    width: 1200px;
    height: 858px;
    overflow: hidden;
    background: var(--stage);
    font-family: "Roboto", Arial, sans-serif;
  }
  .card {
    position: absolute;
    left: 250px;
    width: 700px;
    height: 400px;
    background: var(--paper);
    overflow: hidden;
    box-shadow: 0 4px 14px rgba(0,0,0,0.12);
  }
  .card--front { top: 19px; }
  .card--back { top: 439px; }
  .card__art {
    position: absolute;
    inset: 0;
    width: 100%;
    height: 100%;
  }

  /* front */
  .contact {
    position: absolute;
    right: 145px;
    top: 38px;
    text-align: right;
    white-space: nowrap;
  }
  .contact__name {
    font-weight: 700;
    font-size: 34px;
    color: var(--gold);
    letter-spacing: 0.5px;
  }
  .contact__line {
    font-weight: 300;
    font-size: 17px;
    color: var(--ink);
    margin-top: 10px;
  }
  .contact__icons {
    position: absolute;
    right: 70px;
    top: 44px;
    display: flex;
    flex-direction: column;
    gap: 10px;
  }
  .contact__icon { width: 22px; height: 22px; display: block; }
  .brand {
    position: absolute;
    left: 28px;
    top: 262px;
    display: flex;
    align-items: center;
    gap: 10px;
  }
  .brand__dot {
    width: 52px;
    height: 52px;
    border-radius: 50%;
    background: var(--gold);
  }
  .brand__name {
    font-weight: 700;
    font-size: 17px;
    line-height: 1.15;
    color: var(--ink);
    width: 120px;
  }
  .address {
    position: absolute;
    right: 34px;
    bottom: 28px;
    font-weight: 300;
    font-size: 17px;
    color: var(--gold);
    white-space: nowrap;
  }

  /* back */
  .company {
    position: absolute;
    right: 36px;
    top: 40px;
    font-family: "Roboto Condensed", "Arial Narrow", sans-serif;
    font-weight: 700;
    font-size: 38px;
    color: var(--ink);
    white-space: nowrap;
  }
  .tagline {
    position: absolute;
    left: 34px;
    bottom: 30px;
    font-family: "Roboto Condensed", "Arial Narrow", sans-serif;
    font-weight: 700;
    font-size: 28px;
    letter-spacing: 1px;
    color: var(--ink);
    white-space: nowrap;
  }
</style>
</head>
<body>

<section class="card card--front">
  <svg class="card__art" viewBox="0 0 700 400" role="img" aria-label="Black city skyline silhouette rising from left to right">
    <polygon points="210,400 700,90 700,400" fill="var(--ink)"/>
  </svg>

  <div class="contact">
    <p class="contact__name">Dwight Kallum</p>
    <p class="contact__line">305-271-5589</p>
    <p class="contact__line">harborlanerealtyinc@mailnest.com</p>
  </div>

  <div class="contact__icons">
    <svg class="contact__icon" viewBox="0 0 22 22" aria-label="Phone">
      <rect width="22" height="22" fill="var(--gold)"/>
      <path d="M7 5 l3 3 -1.5 2 a8 8 0 0 0 3.5 3.5 l2 -1.5 3 3 -2 2 C9 16 6 13 5 7 z" fill="var(--ink)"/>
    </svg>
    <svg class="contact__icon" viewBox="0 0 22 22" aria-label="Email">
      <rect width="22" height="22" fill="var(--gold)"/>
      <rect x="4" y="6" width="14" height="10" fill="none" stroke="var(--ink)" stroke-width="1.6"/>
      <path d="M4 6 l7 6 7 -6 M4 16 l5 -5 M18 16 l-5 -5" fill="none" stroke="var(--ink)" stroke-width="1.6"/>
    </svg>
  </div>

  <div class="brand">
    <span class="brand__dot"></span>
    <span class="brand__name">Harbor Lane Realty Inc</span>
  </div>

  <p class="address">PO Box 718296 Coral Mill Key FL 33071</p>
</section>

<section class="card card--back">
  <svg class="card__art" viewBox="0 0 700 400" role="img" aria-label="Yellow city skyline silhouette descending from left to right">
    <defs>
      <linearGradient id="skyline-gold" x1="0" y1="0" x2="1" y2="1">
        <stop offset="0" stop-color="var(--gold-deep)"/>
        <stop offset="1" stop-color="var(--gold)"/>
      </linearGradient>
    </defs>
    <polygon points="0,40 0,400 520,400" fill="url(#skyline-gold)"/>
  </svg>

  <h1 class="company">Harbor Lane Realty Inc</h1>
  <p class="tagline">BUY HOUSES CASH</p>
</section>

</body>
</html>
```